Road Construction Company needs business cards

We would like a new business card designed for our business.

We're a road construction company based in Qld, Australia.

Can the business card please have the following information on it.

Name: Warren Halbeck
Position: General Manager
Phone: 0472 915 348
Email: Warren.halbeck@tovrin.com.au
Address: 87 Marrow Ave, Pendlebay, QLD, 4023
Website: www.tovrin.com.au

Visually we'd like the card to be professional and simple.

Attached is our logo.

Our website is www.tovrin.com.au

Target Market(s)

Men aged 25-60

Contact Information for Business Card

As listed in project description

Font styles to use
Serif

Requirements
Must have
• Large logo on back of card

```html
<!DOCTYPE html>
<html lang="en">
<head>
<meta charset="utf-8">
<title>Tovrin Road Construction – Business Card</title>
<link rel="stylesheet" href="https://fonts.googleapis.com/css2?family=Lato:wght@400;700;900&display=swap">
<style>
  :root{
    --stage:#2a2a2b;
    --card-dark:#1b1b1c;
    --card-light:#ffffff;
    --brand-blue:#0656a3;
    --accent-blue:#34a4d8;
    --logo-blue:#1f63b5;
    --ink:#1e1e1e;
  }
  *{box-sizing:border-box;margin:0;padding:0}
  html,body{width:1200px;height:875px;overflow:hidden}
  body{
    background:var(--stage);
    font-family:"Lato",Arial,sans-serif;
    display:flex;flex-direction:column;align-items:center;justify-content:center;gap:36px;
  }
  .card{
    width:700px;height:389px;position:relative;overflow:hidden;
    box-shadow:0 14px 30px rgba(0,0,0,.45);
  }
  /* back */
  .card-back{background:var(--card-dark);display:flex;align-items:center;justify-content:center}
  .wordmark{
    display:flex;align-items:center;gap:18px;
    color:var(--logo-blue);font-weight:900;font-size:44px;letter-spacing:1px;text-transform:uppercase;
  }
  .wordmark-square{width:34px;height:34px;background:var(--logo-blue)}
  /* front */
  .card-front{background:var(--card-light)}
  .brand-panel{position:absolute;top:0;right:0;width:262px;height:100%;background:var(--brand-blue)}
  .contact-block{position:absolute;left:62px;top:118px}
  .person-name{
    color:var(--brand-blue);font-weight:900;font-size:31px;letter-spacing:.3px;text-transform:uppercase;line-height:1;
  }
  .person-role{color:var(--accent-blue);font-size:19px;margin-top:6px}
  .details{list-style:none;margin-top:26px;color:var(--ink);font-size:16px;line-height:1.4}
  .details li{display:flex;align-items:flex-start;gap:12px;margin-bottom:6px}
  .details svg{width:15px;height:15px;margin-top:3px;flex:none;fill:var(--brand-blue)}
</style>
</head>
<body>
  <section class="card card-back">
    <div class="wordmark"><span class="wordmark-square"></span><span>Tovrin Road Construction</span></div>
  </section>

  <section class="card card-front">
    <div class="contact-block">
      <h1 class="person-name">Warren Halbeck</h1>
      <p class="person-role">General Manager</p>
      <ul class="details">
        <li>
          <svg viewBox="0 0 16 16"><path d="M8 0a5.5 5.5 0 0 0-5.5 5.5C2.5 10 8 16 8 16s5.5-6 5.5-10.5A5.5 5.5 0 0 0 8 0zm0 7.8a2.3 2.3 0 1 1 0-4.6 2.3 2.3 0 0 1 0 4.6z"/></svg>
          <span>87 Marrow Ave,<br>Pendlebay, QLD, 4023</span>
        </li>
        <li>
          <svg viewBox="0 0 16 16"><path d="M3.6 1l2.3 3.2-1.4 1.6a9 9 0 0 0 5.7 5.7l1.6-1.4L15 12.4 13.3 15C6.5 14.5 1.5 9.5 1 2.7z"/></svg>
          <span>0472 915 348</span>
        </li>
        <li>
          <svg viewBox="0 0 16 16"><path d="M1 3h14v10H1zm1.5 1.2v.3L8 8.6l5.5-4.1v-.3z"/></svg>
          <span>Warren.halbeck@tovrin.com.au</span>
        </li>
        <li>
          <svg viewBox="0 0 16 16"><path d="M8 1a7 7 0 1 0 0 14A7 7 0 0 0 8 1zm0 1.6c.9 0 1.9 1.9 2.1 4.6H5.9C6.1 4.5 7.1 2.6 8 2.6zM5.9 8.8h4.2c-.2 2.7-1.2 4.6-2.1 4.6s-1.9-1.9-2.1-4.6z"/></svg>
          <span>www.tovrin.com.au</span>
        </li>
      </ul>
    </div>
    <div class="brand-panel"></div>
  </section>
</body>
</html>
```